Business card design for Virtual Assistance company

I need a business card designed for my virtual assistance company. We are a small company who services primarily C-level executive clients. The card needs to be double sided with the following contact information on the back:
Melissa Thornbury
Owner/CEO
info@rkpadvisory.net
www.rkpadvisory.net
555.302.9817

The front side should just have the company name incorporated: "RKP Advisory" and "virtual assistance"

The card should be simplistic, but eye catching and should speak to high level executives. Our primary focus areas consist of executive assistance and government contracting.

Target Market(s)

CEOs and executives

Contact Information for Business Card

see project description. phone, email, website.

Colors

Designer to choose only greyscale colors for use in the design.

```html
<!DOCTYPE html>
<html lang="en">
<head>
<meta charset="utf-8">
<title>RKP Advisory – Business Card</title>
<link rel="stylesheet" href="https://fonts.googleapis.com/css2?family=Cinzel:wght@600&family=Poppins:wght@300;400&display=swap">
<style>
  :root {
    --canvas: #1c1c1c;
    --card: #0d0d0d;
    --accent: #c4c4c4;
    --edge: #9a9a9a;
    --white: #f4f4f4;
    --silver: #d2d2d2;
    --divider: #3a3a3a;
  }
  * { margin: 0; padding: 0; box-sizing: border-box; }
  html, body { width: 1200px; height: 900px; overflow: hidden; }
  body {
    background: var(--canvas);
    position: relative;
    font-family: "Poppins", sans-serif;
  }
  .card {
    position: absolute;
    width: 540px;
    height: 308px;
    background: var(--card);
    border-radius: 18px;
    border-bottom: 5px solid var(--edge);
    overflow: hidden;
  }
  .card--contact { left: 50px; top: 470px; display: flex; align-items: center; }
  .card--brand { left: 610px; top: 120px; display: flex; flex-direction: column; align-items: center; justify-content: center; }

  .brand-block {
    width: 260px;
    display: flex;
    justify-content: center;
    align-items: center;
  }
  .brand-name {
    font-family: "Cinzel", serif;
    font-weight: 600;
    color: var(--accent);
    font-size: 30px;
    letter-spacing: 2px;
    line-height: 1.15;
    text-align: center;
  }
  .divider {
    width: 1px;
    height: 170px;
    background: var(--divider);
  }
  .details { padding-left: 30px; padding-right: 20px; color: var(--white); }
  .person-name {
    font-family: "Cinzel", serif;
    font-weight: 600;
    color: var(--accent);
    font-size: 19px;
    letter-spacing: 1px;
    white-space: nowrap;
  }
  .person-title { font-size: 14px; font-weight: 300; margin-bottom: 22px; }
  .contact-list { list-style: none; }
  .contact-list li {
    display: flex;
    align-items: center;
    gap: 10px;
    font-size: 14px;
    font-weight: 300;
    line-height: 1.75;
    white-space: nowrap;
  }
  .contact-list svg { width: 14px; height: 14px; fill: var(--accent); flex: none; }

  .brand-name--large {
    color: var(--silver);
    font-size: 46px;
    letter-spacing: 4px;
  }
  .tagline {
    margin-top: 10px;
    color: var(--silver);
    font-size: 13px;
    letter-spacing: 4px;
    text-transform: uppercase;
  }
</style>
</head>
<body>

  <section class="card card--brand">
    <div class="brand-name brand-name--large">RKP Advisory</div>
    <div class="tagline">Virtual Assistance</div>
  </section>

  <section class="card card--contact">
    <div class="brand-block">
      <div class="brand-name">RKP<br>Advisory</div>
    </div>
    <div class="divider"></div>
    <div class="details">
      <div class="person-name">Melissa Thornbury</div>
      <div class="person-title">Owner/CEO</div>
      <ul class="contact-list">
        <li>
          <svg viewBox="0 0 24 24" aria-hidden="true"><path d="M6.6 10.8a15.1 15.1 0 0 0 6.6 6.6l2.2-2.2a1 1 0 0 1 1-.25 11.4 11.4 0 0 0 3.6.57 1 1 0 0 1 1 1V20a1 1 0 0 1-1 1A17 17 0 0 1 3 4a1 1 0 0 1 1-1h3.5a1 1 0 0 1 1 1c0 1.25.2 2.45.57 3.6a1 1 0 0 1-.25 1z"/></svg>
          555.302.9817
        </li>
        <li>
          <svg viewBox="0 0 24 24" aria-hidden="true"><path d="M2 5h20v14H2zm2 2v.4l8 5.2 8-5.2V7zm0 2.8V17h16V9.8l-8 5.2z"/></svg>
          info@rkpadvisory.net
        </li>
        <li>
          <svg viewBox="0 0 24 24" aria-hidden="true"><path d="M12 2a10 10 0 1 0 0 20 10 10 0 0 0 0-20zm6.9 6h-2.9a15.6 15.6 0 0 0-1.4-3.6A8 8 0 0 1 18.9 8zM12 4c.8 1.2 1.5 2.5 1.9 4h-3.8c.4-1.5 1.1-2.8 1.9-4zM4.3 14a8 8 0 0 1 0-4h3.4a16.5 16.5 0 0 0 0 4zm.8 2h2.9c.3 1.3.8 2.5 1.4 3.6A8 8 0 0 1 5.1 16zM8 8H5.1a8 8 0 0 1 4.3-3.6C8.8 5.5 8.3 6.7 8 8zm4 12c-.8-1.2-1.5-2.5-1.9-4h3.8c-.4 1.5-1.1 2.8-1.900 4zm2.3-6H9.7a14.7 14.7 0 0 1 0-4h4.6a14.7 14.7 0 0 1 0 4zm.3 5.6c.6-1.1 1.1-2.3 1.4-3.6h2.9a8 8 0 0 1-4.3 3.6zm1.7-5.6a16.5 16.5 0 0 0 0-4h3.4a8 8 0 0 1 0 4z"/></svg>
          www.rkpadvisory.net
        </li>
      </ul>
    </div>
  </section>

</body>
</html>
```